Step and Repeat Backdrop for wedding reception photo booth

Would like to have a Step and Repeat Backdrop (8 foot high by 10 foot wide) that incorporates the wedding logo (attached) and the names Helen and Gavin. Background should be white, and wedding colors are burgundy and gold. Show me creativity :-) I have included some random samples.

```html
<!DOCTYPE html>
<html lang="en">
<head>
<meta charset="utf-8">
<title>Helen &amp; Gavin — Step and Repeat Backdrop</title>
<link rel="stylesheet" href="https://fonts.googleapis.com/css2?family=Playfair+Display:wght@600&family=Cormorant+Garamond:wght@600&display=swap">
<style>
  :root {
    --page: #f4f4f5;
    --burgundy: #8e1334;
    --gold-deep: #d8961f;
    --gold: #f2c230;
    --gold-light: #f6ec8e;
  }
  html, body {
    margin: 0;
    padding: 0;
    width: 1200px;
    height: 1200px;
    overflow: hidden;
    background: var(--page);
  }
  .backdrop {
    position: absolute;
    left: 0;
    top: 120px;
    width: 1200px;
    height: 960px;
    display: block;
  }
  .backdrop__field { fill: var(--burgundy); }
  .tile__mark {
    font-family: "Playfair Display", Georgia, serif;
    font-weight: 600;
    font-size: 40px;
    fill: var(--gold);
    text-anchor: middle;
  }
  .tile__ornament { fill: var(--gold); opacity: 0.3; }
  .crest__frame {
    fill: none;
    stroke: url(#goldSheen);
    stroke-width: 7;
    stroke-linejoin: miter;
  }
  .crest__frame--inner { stroke-width: 4; }
  .crest__ornament { fill: var(--gold); opacity: 0.25; }
  .crest__floral { fill: var(--gold); opacity: 0.25; }
  .crest__monogram {
    font-family: "Playfair Display", Georgia, serif;
    font-weight: 600;
    font-size: 172px;
    fill: url(#goldSheen);
    text-anchor: middle;
  }
  .crest__ribbon { fill: url(#goldSheen); }
  .crest__names {
    font-family: "Cormorant Garamond", Georgia, serif;
    font-weight: 600;
    font-size: 30px;
    letter-spacing: 12px;
    fill: var(--burgundy);
    text-anchor: middle;
  }
  .crest__ring { fill: none; stroke: var(--burgundy); stroke-width: 2.5; }
</style>
</head>
<body>
<svg class="backdrop" viewBox="0 0 1200 960" xmlns="http://www.w3.org/2000/svg" aria-label="Helen and Gavin wedding step and repeat backdrop">
  <defs>
    <linearGradient id="goldSheen" x1="0" y1="0" x2="1" y2="0">
      <stop offset="0" stop-color="#d8961f"/>
      <stop offset="0.45" stop-color="#f2c230"/>
      <stop offset="0.75" stop-color="#f6ec8e"/>
      <stop offset="1" stop-color="#e9b92a"/>
    </linearGradient>
    <g id="repeatTile">
      <rect class="tile__ornament" x="-50" y="-50" width="100" height="24" rx="12" role="img" aria-label="Gold scroll flourish ornament"/>
      <text class="tile__mark" x="0" y="14">H&amp;G</text>
      <rect class="tile__ornament" x="-50" y="26" width="100" height="24" rx="12" role="img" aria-label="Gold scroll flourish ornament"/>
    </g>
  </defs>

  <rect class="backdrop__field" x="0" y="0" width="1200" height="960"/>

  <g class="repeat-pattern">
    <use href="#repeatTile" x="77" y="81"/>
    <use href="#repeatTile" x="286" y="81"/>
    <use href="#repeatTile" x="495" y="81"/>
    <use href="#repeatTile" x="704" y="81"/>
    <use href="#repeatTile" x="914" y="81"/>
    <use href="#repeatTile" x="1122" y="81"/>

    <use href="#repeatTile" x="77" y="242"/>
    <use href="#repeatTile" x="286" y="242"/>
    <use href="#repeatTile" x="914" y="242"/>
    <use href="#repeatTile" x="1122" y="242"/>

    <use href="#repeatTile" x="77" y="404"/>
    <use href="#repeatTile" x="1122" y="404"/>
    <use href="#repeatTile" x="77" y="565"/>
    <use href="#repeatTile" x="1122" y="565"/>
    <use href="#repeatTile" x="77" y="727"/>
    <use href="#repeatTile" x="1122" y="727"/>

    <use href="#repeatTile" x="77" y="888"/>
    <use href="#repeatTile" x="286" y="888"/>
    <use href="#repeatTile" x="495" y="888"/>
    <use href="#repeatTile" x="704" y="888"/>
    <use href="#repeatTile" x="914" y="888"/>
    <use href="#repeatTile" x="1122" y="888"/>
  </g>

  <g class="crest">
    <polygon class="crest__frame" points="600,145 840,245 940,485 840,725 600,825 360,725 260,485 360,245"/>
    <polygon class="crest__frame crest__frame--inner" points="719,199 886,366 886,604 719,771 481,771 314,604 314,366 481,199"/>

    <rect class="crest__ornament" x="440" y="262" width="320" height="86" rx="36" role="img" aria-label="Gold scroll flourish with fleur-de-lis"/>
    <text class="crest__monogram" x="600" y="516">H&amp;G</text>
    <rect class="crest__ornament" x="440" y="546" width="320" height="86" rx="36" role="img" aria-label="Gold scroll flourish with fleur-de-lis"/>

    <rect class="crest__floral" x="228" y="644" width="88" height="112" rx="40" role="img" aria-label="Gold floral spray"/>
    <rect class="crest__floral" x="884" y="644" width="88" height="112" rx="40" role="img" aria-label="Gold floral spray"/>

    <rect class="crest__ribbon" x="386" y="669" width="428" height="78"/>
    <text class="crest__names" x="600" y="718">Helen&#160;&#160;&#160;&#160;Gavin</text>
    <circle class="crest__ring" cx="598" cy="709" r="10"/>
  </g>
</svg>
</body>
</html>
```